TLK Electricial Contracting Services

Hi guys, after a design for my small electrical company, have logo design files to be incorporated into the layout, the basic concept is electrical contracting services for residential, commercial, industrial & data services, image is clean clear and strong,

Card format is to have a nice clean logo on front,with maybe the Residential – commercial – industrial - data, followed with licensed & insured, followed by contact details on backside of the card.

Target Market(s)

Residential, commercial, industrial sectors.

Industry/Entity Type

Electrical

Contact Information for Business Card

TLK logo,
Residential – commercial – industrial - data
REC: 61307
Email: tlk@vornamail.net.au
Phone: 0487 352 019

Requirements
Must have
• Clean & strong design.
Nice to have
• If possible, I would like the logo colours inverted so the text is orange and the background is black on the front of the card, then the backside of the card be the reverse colour
Should not have
• No Sparks, lightning bolts,

```html
<!DOCTYPE html>
<html lang="en">
<head>
<meta charset="utf-8">
<title>TLK Electrical Contracting Services – Business Card</title>
<link rel="stylesheet" href="https://fonts.googleapis.com/css2?family=Open+Sans:wght@400;600;700&display=swap">
<style>
  :root {
    --backdrop: #3a302b;
    --card-black: #1c1c1c;
    --card-black-deep: #121212;
    --orange: #f58220;
    --white: #ffffff;
    --silver: #d6d6d6;
    --divider: #4a4a4a;
  }
  * { margin: 0; padding: 0; box-sizing: border-box; }
  html, body {
    width: 1200px;
    height: 844px;
    overflow: hidden;
    background: var(--backdrop);
    font-family: "Open Sans", Arial, sans-serif;
  }
  .stage {
    position: relative;
    width: 1200px;
    height: 844px;
    display: flex;
    align-items: center;
    justify-content: center;
    gap: 40px;
  }
  .card {
    position: relative;
    width: 540px;
    height: 309px;
    background: var(--card-black);
    box-shadow: 0 10px 30px rgba(0,0,0,.45);
  }

  /* Details side */
  .brand {
    position: absolute;
    top: 38px;
    left: 150px;
    width: 300px;
    text-align: right;
  }
  .brand-mark {
    display: flex;
    align-items: center;
    justify-content: flex-end;
    gap: 12px;
    color: var(--orange);
    font-weight: 700;
    font-size: 88px;
    line-height: 1;
    letter-spacing: -2px;
  }
  .brand-mark .square {
    width: 22px;
    height: 22px;
    background: var(--orange);
  }
  .brand-name {
    margin-top: 6px;
    color: var(--orange);
    font-weight: 600;
    font-size: 19px;
  }
  .person {
    position: absolute;
    left: 40px;
    top: 184px;
    width: 200px;
    text-align: right;
    color: var(--white);
  }
  .person-name { color: var(--orange); font-weight: 600; font-size: 19px; line-height: 1.2; }
  .person-role { font-size: 13px; margin-bottom: 10px; }
  .person-address { font-size: 14px; line-height: 1.25; }
  .divider {
    position: absolute;
    left: 258px;
    top: 172px;
    width: 1px;
    height: 102px;
    background: var(--divider);
  }
  .contacts {
    position: absolute;
    left: 274px;
    top: 170px;
    list-style: none;
    color: var(--white);
    font-size: 14px;
  }
  .contacts li {
    display: flex;
    align-items: center;
    gap: 10px;
    height: 26px;
  }
  .contacts .icon {
    width: 16px;
    height: 16px;
    background: var(--orange);
    display: flex;
    align-items: center;
    justify-content: center;
    border-radius: 2px;
  }

  /* Logo side */
  .card-logo-side {
    background: var(--card-black-deep);
    display: flex;
    align-items: center;
    justify-content: center;
  }
  .logo-side-mark {
    color: var(--silver);
    font-weight: 700;
    font-size: 96px;
    letter-spacing: -2px;
  }
</style>
</head>
<body>
<main class="stage">
  <section class="card card-details" aria-label="Card details side">
    <div class="brand">
      <div class="brand-mark"><span class="square"></span>TLK</div>
      <div class="brand-name">Theo Lark Electrical</div>
    </div>

    <div class="person">
      <div class="person-name">Daniel Hurst</div>
      <div class="person-role">Managing Director</div>
      <div class="person-address">12345, Address Goes Here<br>Country Name, 123456</div>
    </div>

    <div class="divider"></div>

    <ul class="contacts">
      <li>
        <span class="icon"><svg width="10" height="10" viewBox="0 0 10 10"><path d="M2 1h2l1 2-1.2 1a5 5 0 0 0 2.2 2.2L7 5l2 1v2c0 .6-.4 1-1 1A8 8 0 0 1 1 2c0-.6.4-1 1-1z" fill="#fff"/></svg></span>
        (044)-456-7890
      </li>
      <li>
        <span class="icon"><svg width="10" height="10" viewBox="0 0 10 10"><rect x="2.5" y="0.5" width="5" height="9" rx="1" fill="none" stroke="#fff"/><circle cx="5" cy="7.8" r=".6" fill="#fff"/></svg></span>
        123-456-7890
      </li>
      <li>
        <span class="icon"><svg width="10" height="10" viewBox="0 0 10 10"><rect x="0.5" y="2" width="9" height="6" fill="none" stroke="#fff"/><path d="M.5 2 5 5.5 9.5 2" fill="none" stroke="#fff"/></svg></span>
        info@youremail.com
      </li>
      <li>
        <span class="icon"><svg width="10" height="10" viewBox="0 0 10 10"><path d="M4 6 6 4M3.5 4.5 2 6a1.4 1.4 0 0 0 2 2l1.5-1.5M6.5 5.5 8 4a1.4 1.4 0 0 0-2-2L4.5 3.5" fill="none" stroke="#fff" stroke-width="1.1" stroke-linecap="round"/></svg></span>
        www.website.com
      </li>
    </ul>
  </section>

  <section class="card card-logo-side" aria-label="Card logo side">
    <div class="logo-side-mark">TLK</div>
  </section>
</main>
</body>
</html>
```